Harrowmere Freight, Project

Company Profile
Harrowmere Freight Sdn Bhd is a well established and experienced freight forwarder in Kuala Lumpur, Malaysia. We specialize in air and sea forwarding, Custom Brokerage and regulatory compliance services, inland transportation,
overseas freighting and warehousing and distribution management. With our dedicated qualified and experienced professionals, we are fully committed to serving our clients.

Our Mission
Based on the motto “Quick, Reliable and Polite”, Harrowmere Freight is dedicated to upholding the following three points corporate philosophy:
1. Adhering to the principle that “the customer always comes first”.
2. Contributing to the development of the local community.
3. Making it our duty to be responsible and sincere.

Our Edge
• One-Stop Logistics Solutions
• Extensive Network Throughout Malaysia
• Highly Qualified and Experienced Pool of Professionals
• Comprehensive IT Solutions
• Innovative and Customer-focused Solutions
• Flexible and Consistent in Managing Exceptions
• Total Supply Chain Visibility

Target Market(s)

We sell the logistics services to all the industry in Malaysia. (ONE Stop Logistics Solutions)

Industry/Entity Type

Logistic

Contact Information for Business Card

I want the back of the card to be white with the logo and slogan. i would like to see the logo on the front with the general info.

Requirements
Must have
• Name, Title, Office, Cell, Fax, Email, Address, Website
Nice to have
• Modern Design Business Card

```html
<!DOCTYPE html>
<html lang="en">
<head>
<meta charset="utf-8">
<title>Harrowmere Freight Stationery</title>
<link href="https://fonts.googleapis.com/css2?family=Roboto:wght@400;500;700&family=Roboto+Condensed:wght@700&display=swap" rel="stylesheet">
<style>
:root{
  --stage:#d0d0d0;
  --paper:#f7f7f7;
  --blue:#2f6aa8;
  --blue-light:#3796d3;
  --blue-deep:#2f5fa5;
  --ink:#33302f;
  --text:#3a3a3a;
  --grey:#5a5a5a;
  --white:#ffffff;
}
*{margin:0;padding:0;box-sizing:border-box}
html,body{width:1198px;height:1200px;overflow:hidden}
body{background:var(--stage);font-family:"Roboto",sans-serif;color:var(--text);position:relative}
.sheet{position:absolute;background:var(--paper);box-shadow:0 1px 3px rgba(0,0,0,.25);overflow:hidden}
.footer-band{position:absolute;left:0;right:0;bottom:0;background:var(--ink)}
.footer-rule{position:absolute;left:0;right:0;background:var(--blue)}
.brand{font-family:"Roboto",sans-serif;font-weight:500;color:var(--grey);line-height:1.05;display:flex;align-items:center;gap:6px}
.brand-mark{width:9px;height:9px;background:var(--blue);flex:none}
.slogan{position:absolute;color:var(--white);font-weight:700;letter-spacing:.04em;text-transform:uppercase}
.company{font-family:"Roboto Condensed",sans-serif;font-weight:700;color:var(--blue);text-transform:uppercase}
.company small{font-family:"Roboto",sans-serif;font-weight:400;color:var(--text);text-transform:none}
.contact-list{list-style:none}
.contact-list li{display:flex;align-items:center;gap:5px}
.contact-list svg{flex:none}

/* letterhead */
.letterhead{left:88px;top:49px;width:485px;height:686px}
.letterhead .brand{position:absolute;left:39px;top:82px;font-size:15px}
.letterhead .contact-list{position:absolute;left:319px;top:60px;font-size:7px;line-height:9px}
.letterhead .footer-info{position:absolute;left:39px;top:560px;font-size:7px;line-height:10px}
.letterhead .company{font-size:9.5px;margin-bottom:5px}
.letterhead .gst{color:var(--blue);font-weight:500;margin-top:6px}
.letterhead .gst span{font-weight:400}
.letterhead .footer-rule{top:620px;height:4px}
.letterhead .footer-band{height:56px}
.letterhead .slogan{right:32px;top:654px;font-size:8px}

/* folder */
.folder{left:625px;top:49px;width:485px;height:686px;background:linear-gradient(180deg,var(--blue-light),var(--blue-deep))}
.folder .spine{position:absolute;top:0;bottom:0;width:1px;background:rgba(20,60,120,.45)}
.folder .brand{position:absolute;left:0;right:0;top:380px;justify-content:center;color:var(--white);font-size:30px}
.folder .brand-mark{background:var(--white);width:16px;height:16px}

/* envelopes */
.envelope-back{left:170px;top:773px;width:590px;height:265px;background:var(--paper)}
.envelope-back .flap{position:absolute;left:0;top:0;width:100%;height:88px}
.envelope-back .web{position:absolute;left:0;right:0;top:40px;text-align:center;color:var(--white);font-size:7.5px;letter-spacing:.05em}
.envelope-front{left:121px;top:885px;width:586px;height:266px}
.envelope-front .brand{position:absolute;left:29px;top:78px;font-size:13px}
.envelope-front .address{position:absolute;left:29px;top:116px;font-size:7px;line-height:10px}
.envelope-front .footer-rule{top:214px;height:4px}
.envelope-front .footer-band{height:44px}
.envelope-front .slogan{right:24px;top:240px;font-size:8px}

/* cards */
.card{left:867px;width:210px;height:127px}
.card .brand{position:absolute;right:10px;font-size:10px;text-align:right}
.card .brand-mark{width:6px;height:6px}
.card .footer-rule{top:98px;height:2px}
.card .footer-band{height:24px}
.card .slogan{right:9px;top:108px;font-size:5px;line-height:7px;text-align:right}
.card-services{top:797px}
.card-services .brand{top:42px}
.card-services h3{position:absolute;left:13px;top:12px;font-family:"Roboto Condensed",sans-serif;font-size:7px;color:var(--blue)}
.card-services ul{position:absolute;left:13px;top:24px;list-style:none;font-size:4.6px;line-height:7px;color:var(--text)}
.card-services li::before{content:"\00BB";color:var(--blue);margin-right:3px}
.card-contact{top:963px}
.card-contact .accent{position:absolute;left:0;top:13px;width:2px;height:22px;background:var(--blue)}
.card-contact .person{position:absolute;left:10px;top:14px}
.card-contact .name{font-size:7.5px;font-weight:700;color:var(--blue)}
.card-contact .role{font-size:4.5px}
.card-contact .mobile{font-size:4.8px;font-weight:700;display:flex;align-items:center;gap:3px;margin-top:2px}
.card-contact .details{position:absolute;left:10px;top:42px;font-size:4.5px;line-height:6px}
.card-contact .company{font-size:6px}
.card-contact .contact-list{margin-top:3px;font-size:4.5px;line-height:6px}
.card-contact .brand{top:50px}
</style>
</head>
<body>

<!-- Letterhead -->
<section class="sheet letterhead">
  <div class="brand"><span class="brand-mark"></span><span>Harrowmere<br>Freight</span></div>
  <ul class="contact-list">
    <li><svg width="6" height="6" viewBox="0 0 10 10"><path fill="#2f6aa8" d="M1 3h8v6H1zM0 2c2-2 8-2 10 0v2H0z"/></svg>(603) 5521 8730 / 8731</li>
    <li><svg width="6" height="6" viewBox="0 0 10 10"><path fill="#2f6aa8" d="M2 0h6v3H2zM0 3h10v5H0zM2 7h6v3H2z"/></svg>(603) 5521 8735</li>
    <li><svg width="6" height="6" viewBox="0 0 10 10"><path fill="#2f6aa8" d="M0 2h10v7H0z"/><path stroke="#fff" fill="none" d="M0 2l5 4 5-4"/></svg>daniel.rahman@harrowmere.com.my</li>
    <li><svg width="6" height="6" viewBox="0 0 10 10"><circle cx="5" cy="5" r="5" fill="#2f6aa8"/></svg>www.harrowmere.com.my</li>
  </ul>
  <div class="footer-info">
    <p class="company">Harrowmere Freight Sdn. Bhd. <small>(Company No. 1204637-K)</small></p>
    <p>No. 8B, 2nd Floor, Jalan Seroja Indah 3, Taman Seroja,<br>41050 Klang, Selangor Darul Ehsan, Malaysia.</p>
    <p class="gst">GST Registration No: <span>000418502973</span></p>
  </div>
  <span class="footer-rule"></span>
  <div class="footer-band"></div>
  <p class="slogan">One Stop Logistics Solutions</p>
</section>

<!-- Presentation folder -->
<section class="sheet folder">
  <span class="spine" style="left:33px"></span>
  <span class="spine" style="left:40px"></span>
  <div class="brand"><span class="brand-mark"></span><span>Harrowmere Freight</span></div>
</section>

<!-- Envelope back -->
<section class="sheet envelope-back">
  <svg class="flap" viewBox="0 0 590 88" preserveAspectRatio="none" aria-hidden="true">
    <path fill="#2f67a0" d="M6 0H590L560 70C553 84 545 88 530 88H70C55 88 48 84 40 70Z"/>
  </svg>
  <p class="web">www.harrowmere.com.my</p>
</section>

<!-- Envelope front -->
<section class="sheet envelope-front">
  <div class="brand"><span class="brand-mark"></span><span>Harrowmere<br>Freight</span></div>
  <p class="address">No. 8B, 2nd Floor, Jalan Seroja Indah 3, Taman Seroja,<br>41050 Klang, Selangor Darul Ehsan, Malaysia.</p>
  <span class="footer-rule"></span>
  <div class="footer-band"></div>
  <p class="slogan">One Stop Logistics Solutions</p>
</section>

<!-- Business card: services -->
<section class="sheet card card-services">
  <h3>We're Specialize In</h3>
  <ul>
    <li>International Shipping (Air / Sea)</li>
    <li>Consolidation  NVOCC</li>
    <li>Project Management</li>
    <li>Supply Chain Management</li>
    <li>Tax Exemption Consultancy</li>
    <li>Custom Brokerage</li>
    <li>Transportation / Haulage</li>
    <li>Warehousing</li>
    <li>Packing  » Marine Insurance</li>
    <li>Distribution  » Door to Door</li>
  </ul>
  <div class="brand"><span class="brand-mark"></span><span>Harrowmere<br>Freight</span></div>
  <span class="footer-rule"></span>
  <div class="footer-band"></div>
  <p class="slogan">One Stop<br>Logistics Solutions</p>
</section>

<!-- Business card: contact -->
<section class="sheet card card-contact">
  <span class="accent"></span>
  <div class="person">
    <p class="name">Daniel Rahman</p>
    <p class="role">Managing Director</p>
    <p class="mobile"><svg width="4" height="5" viewBox="0 0 6 10"><rect x=".5" y=".5" width="5" height="9" rx="1" fill="none" stroke="#2f6aa8"/></svg>+6012-480 2719</p>
  </div>
  <div class="details">
    <p class="company">Harrowmere Freight Sdn. Bhd.</p>
    <p>(Company No. 1204637-K)</p>
    <p>No. 8B, 2nd Floor, Jalan Seroja Indah 3,<br>Taman Seroja, 41050 Klang, Selangor Darul Ehsan, Malaysia.</p>
    <ul class="contact-list">
      <li><svg width="4" height="4" viewBox="0 0 10 10"><path fill="#2f6aa8" d="M1 3h8v6H1zM0 2c2-2 8-2 10 0v2H0z"/></svg>(603) 5521 8730 / 8731</li>
      <li><svg width="4" height="4" viewBox="0 0 10 10"><path fill="#2f6aa8" d="M2 0h6v3H2zM0 3h10v5H0zM2 7h6v3H2z"/></svg>(603) 5521 8735</li>
      <li><svg width="4" height="4" viewBox="0 0 10 10"><path fill="#2f6aa8" d="M0 2h10v7H0z"/></svg>daniel.rahman@harrowmere.com.my</li>
      <li><svg width="4" height="4" viewBox="0 0 10 10"><circle cx="5" cy="5" r="5" fill="#2f6aa8"/></svg>www.harrowmere.com.my</li>
    </ul>
  </div>
  <div class="brand"><span class="brand-mark"></span><span>Harrowmere<br>Freight</span></div>
  <span class="footer-rule"></span>
  <div class="footer-band"></div>
  <p class="slogan">One Stop<br>Logistics Solutions</p>
</section>

</body>
</html>
```